New Business Card Design Project

I need a design for business cards, i am an electrical business called "Corvane Electrical and Communications" i need the cards to be double sided with the company logo on the back (attached) the front needs to say my company name, web site, email address, telephone number, and ABN number and electrical license number. I am open to different arrangements of the information but would like the background to be incorporating something electrical or something that looks smart. open to all additional ideas also.

The company colours are orange and grey see logo attached.

Business Name: Corvane Electrical and Communications
Website: corvaneelectricalandcomms.example.com.au
Email: brent@corvaneelectricalandcomms.example.com.au
Telephone(mobile): 0481209736
ABN: 71208349162
Lic No: 418273D

Target Market(s)

Business entities, Project Managers, Accounts, Clients

Industry/Entity Type

Electrician

Contact Information for Business Card

I need a design for business cards, i am an electrical business called "Corvane Electrical and Communications" i need the cards to be double sided with the company logo on the back (attached) the front needs to say my company name

Font styles to use
Serif
Sans Serif

Colors
f37122
5c5c5c

Requirements
Must have
• Must have the Logo on the back open to different ways of it being on the back but had in mind to keep it central but again open to other options
Nice to have
• A real modern cool background that is eye catching yet contemporary
Should not have
• No backgrounds of a light bulb or plug or anything like that

```html
<!DOCTYPE html>
<html lang="en">
<head>
<meta charset="utf-8">
<title>Corvane Electrical and Communications – Business Cards</title>
<link rel="stylesheet" href="https://fonts.googleapis.com/css2?family=Roboto:wght@400;500;700&display=swap">
<style>
  :root {
    --backdrop: #2a2a2a;
    --card-grey-light: #5c5c5c;
    --card-grey-dark: #474747;
    --amber: #f6a81c;
    --amber-deep: #f39a12;
    --ink-dark: #2f2f2f;
    --ink-light: #f2f2f2;
    --divider: #8a8a8a;
  }
  * { margin: 0; padding: 0; box-sizing: border-box; }
  html, body { width: 1200px; height: 950px; overflow: hidden; }
  body {
    background: var(--backdrop);
    font-family: "Roboto", Arial, sans-serif;
    position: relative;
  }
  .card {
    position: absolute;
    left: 255px;
    width: 690px;
    height: 420px;
    border-radius: 4px;
    overflow: hidden;
    background: linear-gradient(135deg, var(--card-grey-light), var(--card-grey-dark));
    box-shadow: 0 10px 30px rgba(0,0,0,.45);
  }
  .card--back { top: 40px; }
  .card--front { top: 490px; }

  /* back */
  .back-brand {
    position: absolute;
    left: 0; right: 0; top: 140px;
    text-align: center;
    color: var(--ink-light);
    font-weight: 500;
    line-height: 1.1;
  }
  .back-brand__name { display: block; font-size: 64px; letter-spacing: 4px; }
  .back-brand__line { display: block; font-size: 20px; letter-spacing: 1px; margin-top: 6px; }
  .back-web {
    position: absolute;
    right: 40px; bottom: 50px;
    color: var(--amber);
    font-size: 17px;
  }

  /* front */
  .accent-band { position: absolute; inset: 0; }
  .holder {
    position: absolute;
    left: 260px; top: 72px;
    color: var(--ink-dark);
  }
  .holder__name { font-size: 20px; font-weight: 700; letter-spacing: .5px; }
  .holder__role { font-size: 15px; font-weight: 400; margin-top: 2px; }

  .front-brand {
    position: absolute;
    left: 34px; top: 262px;
    width: 240px;
    color: var(--ink-light);
    font-weight: 500;
    line-height: 1.1;
  }
  .front-brand__name { display: block; font-size: 40px; letter-spacing: 2px; }
  .front-brand__line { display: block; font-size: 11.5px; margin-top: 4px; }

  .divider {
    position: absolute;
    left: 286px; top: 250px;
    width: 1px; height: 136px;
    background: var(--divider);
  }
  .contact {
    position: absolute;
    left: 302px; top: 252px;
    list-style: none;
    color: var(--ink-light);
    font-size: 14.5px;
    line-height: 24px;
  }
  .contact li { display: flex; align-items: center; gap: 8px; white-space: nowrap; }
  .contact .icon { width: 14px; height: 14px; flex: none; }
</style>
</head>
<body>

<section class="card card--back" aria-label="Business card back">
  <div class="back-brand">
    <span class="back-brand__name">CORVANE</span>
    <span class="back-brand__line">ELECTRICAL &amp; COMMUNICATIONS</span>
  </div>
  <p class="back-web">corvaneelectricalandcomms.example.com.au</p>
</section>

<section class="card card--front" aria-label="Business card front">
  <svg class="accent-band" width="690" height="420" viewBox="0 0 690 420" aria-hidden="true">
    <defs>
      <linearGradient id="bandFill" x1="0" y1="0" x2="1" y2="1">
        <stop offset="0" stop-color="var(--amber-deep)"/>
        <stop offset="1" stop-color="var(--amber)"/>
      </linearGradient>
    </defs>
    <polygon fill="url(#bandFill)" points="0,0 690,0 690,230 0,128"/>
  </svg>

  <div class="holder">
    <p class="holder__name">BRENT MARLOW</p>
    <p class="holder__role">PRESIDENT</p>
  </div>

  <div class="front-brand">
    <span class="front-brand__name">CORVANE</span>
    <span class="front-brand__line">ELECTRICAL &amp; COMMUNICATIONS</span>
  </div>

  <div class="divider"></div>

  <ul class="contact">
    <li>ABN: 71208349162</li>
    <li>Lic No: 418273D</li>
    <li>
      <svg class="icon" viewBox="0 0 14 14" aria-hidden="true"><rect x="3" y="0.5" width="8" height="13" rx="1.5" fill="var(--amber)"/><rect x="4.5" y="2.5" width="5" height="7" fill="var(--card-grey-dark)"/></svg>
      0481209736
    </li>
    <li>
      <svg class="icon" viewBox="0 0 14 14" aria-hidden="true"><rect x="0.5" y="3" width="13" height="9" rx="1" fill="var(--amber)"/><path d="M1 3.5 L7 8 L13 3.5" fill="none" stroke="var(--card-grey-dark)" stroke-width="1.2"/></svg>
      brent@corvaneelectricalandcomms.example.com.au
    </li>
    <li>
      <svg class="icon" viewBox="0 0 14 14" aria-hidden="true"><circle cx="7" cy="7" r="6.5" fill="var(--amber)"/><path d="M1 7 H13 M7 0.5 C4 4 4 10 7 13.5 M7 0.5 C10 4 10 10 7 13.5" fill="none" stroke="var(--card-grey-dark)" stroke-width="1"/></svg>
      corvaneelectricalandcomms.example.com.au
    </li>
  </ul>
</section>

</body>
</html>
```